Design 4 pages for an event discovery website

This is a contest for the design of 4 pages for an events discovery website. The feature is part of the new sign-up process.

Please see the attached document for a full scope, mockups and the parent category icons.

Target Market(s)

18-35 Australian event goers

Industry/Entity Type

Events

Number of Pages Required

4 page

```html
<!DOCTYPE html>
<html lang="en">
<head>
<meta charset="utf-8">
<title>Gigvista – Link your accounts</title>
<link rel="stylesheet" href="https://fonts.googleapis.com/css2?family=Open+Sans:wght@400;600&display=swap">
<style>
:root{
  --brand:#f5125f;
  --white:#ffffff;
  --panel:rgba(70,70,110,.55);
  --panel-edge:rgba(255,255,255,.45);
  --ok:#9cc43a;
  --error:#f01818;
  --footer:#141414;
  --footer-text:#b4b4b4;
  --chirp:#1d7fbf;
  --snap:#4e413b;
  --tune:#8fc22a;
  --shelf:#2290e0;
}
*{box-sizing:border-box;margin:0;padding:0}
html,body{width:1200px;height:812px;overflow:hidden}
body{font-family:"Open Sans",Arial,sans-serif;position:relative;background:#6a5ad0;color:var(--white)}
.site-header{position:absolute;left:0;top:0;width:1200px;height:92px;background:var(--brand);z-index:2}
.brand-name{position:absolute;left:60px;top:22px;font-size:33px;font-weight:400;letter-spacing:.5px}
.search-box{position:absolute;left:750px;top:25px;width:217px;height:44px;background:var(--white);border-radius:22px;display:flex;align-items:center;padding-left:18px;gap:10px;color:#777;font-size:16px}
.auth-links{position:absolute;left:1005px;top:33px;font-size:17px;display:flex;gap:14px}
.hero-photo{position:absolute;left:0;top:92px;width:1200px;height:613px;
  background:radial-gradient(ellipse at 60% 55%,#3a2f8a 0%,rgba(58,47,138,0) 45%),
  radial-gradient(ellipse at 20% 80%,#e2d6f5 0%,rgba(226,214,245,0) 40%),
  linear-gradient(180deg,#8a8ee0 0%,#7c70d8 40%,#a48ae6 75%,#8a5fd0 100%)}
.intro-panel{position:absolute;left:64px;top:157px;width:1076px;height:270px;background:var(--panel);border:1px solid var(--panel-edge);padding:34px 34px}
.intro-list{list-style:none}
.intro-list li{display:flex;gap:22px;font-size:22px;line-height:33px;margin-bottom:22px;letter-spacing:.2px}
.intro-list svg{flex:none;margin-top:5px}
.account-buttons{position:absolute;left:60px;top:479px}
.account-btn{position:absolute;left:0;width:217px;border-radius:4px;color:var(--white);display:flex;align-items:center;white-space:nowrap;overflow:hidden}
.account-btn .dot{width:18px;height:18px;border-radius:50%;background:rgba(255,255,255,.85);margin:0 9px 0 9px;flex:none}
.btn-chirp{top:0;height:34px;background:var(--chirp);font-size:15px;font-weight:400}
.btn-snap{top:45px;height:33px;background:var(--snap);font-size:12px;font-weight:600}
.btn-tune{top:91px;height:28px;background:var(--tune);font-size:12px;font-weight:600}
.btn-shelf{top:131px;height:37px;background:var(--shelf);font-size:15px;font-weight:600;border-radius:8px}
.btn-snap span,.btn-tune span{flex:1;text-align:center;padding-right:10px}
.status{position:absolute;left:295px;font-size:17px;display:flex;align-items:center;gap:10px;white-space:nowrap}
.status-ok{top:491px;color:var(--ok)}
.status-error{top:572px;color:var(--error)}
.site-footer{position:absolute;left:0;top:705px;width:1200px;height:107px;background:var(--footer);color:var(--footer-text)}
.footer-nav{position:absolute;left:60px;top:28px;font-size:14px;display:flex;gap:16px}
.copyright{position:absolute;left:60px;top:59px;font-size:14px}
.social-links{position:absolute;left:969px;top:28px;display:flex;gap:17px}
.social-links span{width:46px;height:46px;border:1px solid #9a9a9a;border-radius:50%;display:flex;align-items:center;justify-content:center;font-size:12px;color:#bdbdbd}
</style>
</head>
<body>
<header class="site-header">
  <div class="brand-name">Gigvista</div>
  <div class="search-box">
    <svg width="15" height="15" viewBox="0 0 15 15"><circle cx="6" cy="6" r="4.5" fill="none" stroke="#555" stroke-width="2"/><line x1="9.5" y1="9.5" x2="14" y2="14" stroke="#555" stroke-width="2.4"/></svg>
    Search
  </div>
  <nav class="auth-links"><span>Sign up</span><span>|</span><span>Login</span></nav>
</header>

<div class="hero-photo" role="img" aria-label="Blurred concert photo of a performer in purple and blue stage light"></div>

<section class="intro-panel">
  <ul class="intro-list">
    <li><svg width="20" height="20" viewBox="0 0 20 20"><rect x="1.5" y="3.5" width="14" height="14" rx="2" fill="none" stroke="#fff" stroke-width="2.4"/><path d="M5 10l4 4 9-11" fill="none" stroke="#fff" stroke-width="3"/></svg>Step 1 of 5</li>
    <li><svg width="20" height="20" viewBox="0 0 20 20"><rect x="1.5" y="3.5" width="14" height="14" rx="2" fill="none" stroke="#fff" stroke-width="2.4"/><path d="M5 10l4 4 9-11" fill="none" stroke="#fff" stroke-width="3"/></svg>Link in All you&nbsp; Other social media account and music players</li>
    <li><svg width="20" height="20" viewBox="0 0 20 20"><rect x="1.5" y="3.5" width="14" height="14" rx="2" fill="none" stroke="#fff" stroke-width="2.4"/><path d="M5 10l4 4 9-11" fill="none" stroke="#fff" stroke-width="3"/></svg>By Linking Your accounts, we can save you a Lot of timeby automatically determining your Interests</li>
  </ul>
</section>

<div class="account-buttons">
  <div class="account-btn btn-chirp"><i class="dot"></i>Connect with Chirpline</div>
  <div class="account-btn btn-snap"><span>Sign in with Snapfolio</span></div>
  <div class="account-btn btn-tune"><span>Tunestream Listen</span></div>
  <div class="account-btn btn-shelf"><i class="dot"></i>Download on SongShelf</div>
</div>

<div class="status status-ok"><svg width="15" height="12" viewBox="0 0 15 12"><path d="M1 6l4.5 4.5L14 1.5" fill="none" stroke="#9cc43a" stroke-width="3"/></svg>Linked</div>
<div class="status status-error"><svg width="12" height="12" viewBox="0 0 12 12"><path d="M1.5 1.5l9 9M10.5 1.5l-9 9" stroke="#f01818" stroke-width="3"/></svg>We Don't have that Feature Yet But Have Request your interest</div>

<footer class="site-footer">
  <nav class="footer-nav"><span>Home</span><span>|</span><span>Events</span><span>|</span><span>Artists</span><span>|</span><span>Location</span><span>|</span><span>Blog</span><span>|</span><span>Contact</span></nav>
  <div class="copyright">© 2015 All Rights Reserved.</div>
  <div class="social-links"><span>FL</span><span>CL</span><span>SF</span></div>
</footer>
</body>
</html>
```